Meadowlark Property Review is a leading provider of residential appraisal and home inspection products in S

I need a business card/logo designed that obviously describes my business. We are a residential appraisal and home inspection company in Springfield, MO. We offer residential appraisals, home inspection, pest inspection and radon gas measurement. We have been in business for 18 years and hold state certified residential appraisal licenses and OBREX certified home inspection licenses. I have a logo that I really like and will attach, but would be open to new suggestions. I like more modern designs than traditional and would like a two sided card with our services, licenses and qualifications on the back.

```html
<!DOCTYPE html>
<html lang="en">
<head>
<meta charset="utf-8">
<title>Meadowlark Property Review – Business Card</title>
<link href="https://fonts.googleapis.com/css2?family=Open+Sans:wght@400;600;700&display=swap" rel="stylesheet">
<style>
  :root {
    --stage: #000000;
    --card-light: #f3f3f3;
    --brand-orange: #f7941d;
    --ink: #3a3a3a;
    --white: #ffffff;
    --white-soft: rgba(255, 255, 255, 0.55);
  }
  * { margin: 0; padding: 0; box-sizing: border-box; }
  html, body {
    width: 1200px; height: 900px; overflow: hidden;
    background: var(--stage);
    font-family: "Open Sans", Arial, sans-serif;
  }
  .stage { position: relative; width: 1200px; height: 900px; }

  .card {
    position: absolute; top: 200px;
    width: 310px; height: 502px;
  }
  .card--front {
    left: 265px;
    background: var(--card-light);
    border-radius: 70px 0 70px 0;
  }
  .card--back {
    left: 641px;
    background: var(--brand-orange);
    border-radius: 0 70px 0 70px;
  }

  .brand {
    position: absolute; left: 0; right: 0;
    text-align: center;
  }
  .brand__name {
    font-weight: 700;
    font-size: 25px;
    line-height: 1.15;
    letter-spacing: 0.3px;
  }
  .brand__name span { display: block; }
  .brand__line {
    margin: 7px auto 0;
    font-size: 11px;
    font-weight: 400;
    letter-spacing: 3px;
    text-transform: uppercase;
  }
  .card--front .brand { top: 42px; }
  .card--front .brand__name { color: var(--brand-orange); }
  .card--front .brand__line { color: var(--ink); }
  .card--back .brand { top: 332px; }
  .card--back .brand__name { color: var(--white); }
  .card--back .brand__line { color: var(--white); }

  .contact {
    position: absolute; left: 27px; top: 326px;
    color: var(--ink);
  }
  .contact__name {
    color: var(--brand-orange);
    font-size: 18px; font-weight: 600;
    line-height: 24px;
  }
  .contact__role { font-size: 14px; line-height: 20px; margin-bottom: 16px; }
  .contact__address { font-size: 13.5px; line-height: 16px; margin-bottom: 11px; }
  .contact__line {
    display: flex; align-items: center; gap: 7px;
    font-size: 13.5px; line-height: 19px;
  }
  .contact__icon { width: 10px; height: 10px; flex: none; }

  .offer {
    position: absolute; left: 30px; right: 30px; top: 58px;
    color: var(--white);
    text-align: center;
  }
  .offer__heading {
    font-size: 12px; font-weight: 700;
    letter-spacing: 2.5px; text-transform: uppercase;
    margin-bottom: 8px;
  }
  .offer__list { list-style: none; font-size: 13px; line-height: 20px; }
  .offer__rule {
    width: 60px; height: 1px; margin: 16px auto;
    background: var(--white-soft);
  }
</style>
</head>
<body>
  <main class="stage">
    <section class="card card--front" aria-label="Card front">
      <div class="brand">
        <div class="brand__name"><span>Meadowlark</span><span>Property Review</span></div>
        <div class="brand__line">Appraisal &amp; Inspection</div>
      </div>

      <div class="contact">
        <div class="contact__name">JOHN SMITH</div>
        <div class="contact__role">Managing Director</div>
        <div class="contact__address">1234, Address Goes Here<br>Springfield, MO 65806</div>
        <div class="contact__line">
          <svg class="contact__icon" viewBox="0 0 10 10" aria-hidden="true">
            <path fill="#f7941d" d="M1 3.5C1 2 2.5 1.5 5 1.5S9 2 9 3.5L7.6 4.2 7 3.4H3L2.4 4.2Z M2.2 5.2 3.2 4h3.6l1 1.2V8.5H2.2Z"/>
          </svg>
          <span>823-456-7890</span>
        </div>
        <div class="contact__line">
          <svg class="contact__icon" viewBox="0 0 10 10" aria-hidden="true">
            <rect x="0.5" y="2" width="9" height="6.5" fill="#f7941d"/>
            <path d="M0.8 2.3 5 5.6 9.2 2.3" fill="none" stroke="#f3f3f3" stroke-width="0.9"/>
          </svg>
          <span>info@youremail.com</span>
        </div>
      </div>
    </section>

    <section class="card card--back" aria-label="Card back">
      <div class="offer">
        <div class="offer__heading">Services</div>
        <ul class="offer__list">
          <li>Residential Appraisals</li>
          <li>Home Inspection</li>
          <li>Pest Inspection</li>
          <li>Radon Gas Measurement</li>
        </ul>
        <div class="offer__rule"></div>
        <div class="offer__heading">Licenses</div>
        <ul class="offer__list">
          <li>State Certified Residential Appraiser</li>
          <li>OBREX Certified Home Inspector</li>
          <li>18 Years in Business</li>
        </ul>
      </div>

      <div class="brand">
        <div class="brand__name"><span>Meadowlark</span><span>Property Review</span></div>
        <div class="brand__line">Appraisal &amp; Inspection</div>
      </div>
    </section>
  </main>
</body>
</html>
```